Corvane Freight Company Business Card Design

We are a company that delivers natural saltwater (from the ocean) to aquarium companies, restaurants and home marine tanks. I would like a new business card to suit.

Must include Name, company name, abn, contact number and website as well as logo (see attached).

Looking for a design that stands out, has a clean but unique appearance.

Double and single sided entries welcome

Business

• Logo

```html
<!DOCTYPE html>
<html lang="en">
<head>
<meta charset="utf-8">
<title>Corvane Freight Company – Business Cards</title>
<link rel="stylesheet" href="https://fonts.googleapis.com/css2?family=Source+Sans+3:wght@400;600;700&display=swap">
<style>
  :root {
    --stage: #1c1c1c;
    --card-white: #ffffff;
    --deep-blue: #0559a8;
    --sky-blue: #54c8f2;
    --brand-blue: #1b95d6;
    --ink-grey: #555555;
    --rule-grey: #b5b5b5;
  }
  * { box-sizing: border-box; margin: 0; padding: 0; }
  html, body {
    width: 1200px; height: 750px; overflow: hidden;
    background: var(--stage);
    font-family: "Source Sans 3", "Myriad Pro", Arial, sans-serif;
  }
  .canvas { position: relative; width: 1200px; height: 750px; }
  .card {
    position: absolute; width: 516px; height: 294px;
    background: var(--card-white); overflow: hidden;
  }
  .card--front-dark { left: 73px; top: 61px; }
  .card--front-light { left: 607px; top: 61px; }
  .card--back { left: 342px; top: 400px; background: var(--deep-blue); }
  .card__curve { position: absolute; left: 0; top: 0; width: 516px; height: 294px; }

  .brand {
    position: absolute; display: flex; align-items: center; gap: 8px;
    color: var(--brand-blue); font-weight: 600; line-height: 1.02;
  }
  .brand__dot { flex: none; border-radius: 50%; background: currentColor; }
  .brand--small { left: 28px; top: 88px; font-size: 25px; }
  .brand--small .brand__dot { width: 14px; height: 14px; }
  .brand--large {
    left: 0; right: 0; top: 0; bottom: 0; justify-content: center;
    color: var(--card-white); font-size: 50px; gap: 18px;
  }
  .brand--large .brand__dot { width: 30px; height: 30px; }

  .divider {
    position: absolute; top: 55px; width: 2px; height: 116px;
    background: linear-gradient(var(--card-white), var(--rule-grey) 30%, var(--rule-grey) 70%, var(--card-white));
  }
  .card--front-dark .divider { left: 255px; }
  .card--front-light .divider { left: 255px; }

  .contact { position: absolute; left: 276px; color: var(--ink-grey); }
  .card--front-dark .contact { top: 67px; }
  .card--front-light .contact { top: 58px; }
  .contact__name { font-size: 20px; font-weight: 700; line-height: 1.2; }
  .contact__title { font-size: 15px; margin-bottom: 10px; }
  .contact__line {
    display: flex; align-items: center; gap: 7px;
    font-size: 14.5px; color: var(--deep-blue); line-height: 1.25;
  }
  .contact__line svg { width: 10px; height: 10px; flex: none; }
  .contact__address { font-size: 14.5px; color: var(--deep-blue); line-height: 1.3; margin-top: 16px; }

  .footer-text {
    position: absolute; left: 0; right: 0; text-align: center;
  }
  .card--front-dark .footer-text {
    top: 256px; color: var(--card-white); font-size: 13.5px; line-height: 1.25;
  }
  .card--front-light .footer-text {
    top: 257px; color: var(--ink-grey); font-size: 15px;
  }
  .footer-text strong { font-size: 19px; font-weight: 700; }
</style>
</head>
<body>
<main class="canvas">

  <!-- Front, dark band -->
  <section class="card card--front-dark">
    <svg class="card__curve" viewBox="0 0 516 294" aria-hidden="true">
      <path d="M0 192 Q258 300 516 170 L516 294 L0 294 Z" fill="var(--deep-blue)"/>
      <path d="M28 188 Q258 290 500 175 Q258 270 28 188 Z" fill="var(--sky-blue)"/>
    </svg>
    <div class="brand brand--small"><span class="brand__dot"></span><span>Corvane Freight<br>Company</span></div>
    <div class="divider"></div>
    <div class="contact">
      <div class="contact__name">Your Name</div>
      <div class="contact__title">Title</div>
      <div class="contact__line">
        <svg viewBox="0 0 10 10"><path d="M2 1 L4 1 L4.5 3 L3.3 4 Q4.2 5.9 6 6.7 L7 5.5 L9 6 L9 8 Q5 9.5 1 3 Z" fill="var(--ink-grey)"/></svg>
        123-456-7892
      </div>
      <div class="contact__line">
        <svg viewBox="0 0 10 10"><circle cx="5" cy="5" r="4.3" fill="none" stroke="var(--ink-grey)" stroke-width="1.1"/><path d="M0.7 5 H9.3 M5 0.7 V9.3" stroke="var(--ink-grey)" stroke-width="0.9"/></svg>
        www.corvanefreight.com
      </div>
    </div>
    <p class="footer-text">Street Name, City Name ,State, Zip Code<br>ABN: 123456789</p>
  </section>

  <!-- Front, light band -->
  <section class="card card--front-light">
    <svg class="card__curve" viewBox="0 0 516 294" aria-hidden="true">
      <path d="M0 198 Q258 300 516 168 L516 294 L0 294 Z" fill="var(--sky-blue)"/>
      <path d="M30 188 Q258 295 495 178 Q258 275 30 188 Z" fill="var(--deep-blue)"/>
    </svg>
    <div class="brand brand--small"><span class="brand__dot"></span><span>Corvane Freight<br>Company</span></div>
    <div class="divider"></div>
    <div class="contact">
      <div class="contact__line">
        <svg viewBox="0 0 10 10"><path d="M2 1 L4 1 L4.5 3 L3.3 4 Q4.2 5.9 6 6.7 L7 5.5 L9 6 L9 8 Q5 9.5 1 3 Z" fill="var(--ink-grey)"/></svg>
        123-456-7892
      </div>
      <div class="contact__line">
        <svg viewBox="0 0 10 10"><circle cx="5" cy="5" r="4.3" fill="none" stroke="var(--ink-grey)" stroke-width="1.1"/><path d="M0.7 5 H9.3 M5 0.7 V9.3" stroke="var(--ink-grey)" stroke-width="0.9"/></svg>
        www.corvanefreight.com
      </div>
      <p class="contact__address">Street Name, City Name ,<br>State, Zip Code<br>ABN: 123456789</p>
    </div>
    <p class="footer-text"><strong>Your Name,</strong> Title</p>
  </section>

  <!-- Back -->
  <section class="card card--back">
    <div class="brand brand--large"><span class="brand__dot"></span><span>Corvane Freight<br>Company</span></div>
  </section>

</main>
</body>
</html>
```